Business Card for Professional Photographer

I'm looking for an eye catching modern clean design that compliments my logo/ website fonts & colours.
I specialise in architecture, corporate & commercial photography so I'm marketing to professional clients rather than portrait / wedding clients.

I would prefer to not have a solid black design.

My logo brand guide is as follows :

Main front font. : Reislust
Main font colour : #fff
Slogan front font : Ubuntu Bold
Monogram front font : Venti Medium
Container colour : #fff

I need print ready files in pdf .png & .eps formats.

Included in the files below are some screen grabs as reference to font & colours etc.

```html
<!DOCTYPE html>
<html lang="en">
<head>
<meta charset="utf-8">
<title>Quiet Angle – Business Card</title>
<link rel="stylesheet" href="https://fonts.googleapis.com/css2?family=Open+Sans:wght@300;400;700&family=Ubuntu:wght@700&display=swap">
<style>
  :root {
    --page: #e6e6e6;
    --card: #333335;
    --gold: #d4a548;
    --gold-dark: #a97a26;
    --gold-light: #f4d98a;
    --white: #ffffff;
    --shadow: rgba(0, 0, 0, 0.25);
  }
  * { box-sizing: border-box; margin: 0; padding: 0; }
  html, body {
    width: 1200px;
    height: 1125px;
    overflow: hidden;
    background: var(--page);
    font-family: "Open Sans", Arial, sans-serif;
  }
  .sheet {
    width: 1200px;
    height: 1125px;
    display: flex;
    flex-direction: column;
    align-items: center;
    justify-content: center;
    gap: 60px;
  }
  .card {
    position: relative;
    width: 840px;
    height: 480px;
    background: var(--card);
    box-shadow: 0 10px 30px var(--shadow);
    overflow: hidden;
  }
  .card__edge {
    position: absolute;
    left: 0;
    right: 0;
    bottom: 0;
    height: 7px;
    background: linear-gradient(90deg, var(--gold-dark), var(--gold-light) 50%, var(--gold-dark));
  }

  /* Front */
  .brand {
    position: absolute;
    left: 50%;
    top: 50%;
    transform: translate(-50%, -50%);
    display: flex;
    align-items: center;
    gap: 30px;
  }
  .brand__dot {
    width: 74px;
    height: 74px;
    border: 5px solid var(--gold);
    border-radius: 50%;
    flex: none;
  }
  .brand__name {
    font-weight: 300;
    font-size: 40px;
    letter-spacing: 0.22em;
    color: var(--white);
    line-height: 1;
    text-transform: uppercase;
  }
  .brand__tagline {
    margin-top: 10px;
    font-family: "Ubuntu", Arial, sans-serif;
    font-weight: 700;
    font-size: 12px;
    letter-spacing: 0.2em;
    color: var(--gold);
  }

  /* Back */
  .contact {
    position: absolute;
    left: 130px;
    top: 165px;
    display: flex;
    align-items: center;
  }
  .person {
    text-align: right;
    padding-right: 30px;
  }
  .person__name {
    font-weight: 700;
    font-size: 34px;
    letter-spacing: 0.02em;
    color: var(--gold);
    line-height: 1.1;
  }
  .person__role {
    font-size: 22px;
    color: var(--white);
    letter-spacing: 0.04em;
  }
  .divider {
    width: 2px;
    height: 80px;
    background: var(--gold);
  }
  .details {
    list-style: none;
    padding-left: 24px;
  }
  .details__item {
    display: flex;
    align-items: center;
    gap: 8px;
    font-size: 23px;
    color: var(--white);
    line-height: 1.25;
  }
  .details__icon {
    width: 18px;
    height: 18px;
    fill: var(--gold);
    flex: none;
  }
  .address {
    position: absolute;
    left: 0;
    right: 0;
    bottom: 60px;
    text-align: center;
    font-size: 24px;
    color: var(--white);
    letter-spacing: 0.02em;
  }
</style>
</head>
<body>
<main class="sheet">

  <section class="card card--front" aria-label="Card front">
    <div class="brand">
      <span class="brand__dot"></span>
      <div>
        <div class="brand__name">Quiet Angle</div>
        <div class="brand__tagline">Architecture Corporate Commercial</div>
      </div>
    </div>
    <div class="card__edge"></div>
  </section>

  <section class="card card--back" aria-label="Card back">
    <div class="contact">
      <div class="person">
        <div class="person__name">DANIEL HARTWELL</div>
        <div class="person__role">Director</div>
      </div>
      <div class="divider"></div>
      <ul class="details">
        <li class="details__item">
          <svg class="details__icon" viewBox="0 0 24 24" aria-hidden="true"><path d="M6.6 10.8a15.1 15.1 0 0 0 6.6 6.6l2.2-2.2a1 1 0 0 1 1-.25 11.4 11.4 0 0 0 3.6.57 1 1 0 0 1 1 1V20a1 1 0 0 1-1 1A17 17 0 0 1 3 4a1 1 0 0 1 1-1h3.5a1 1 0 0 1 1 1c0 1.25.2 2.45.57 3.57a1 1 0 0 1-.25 1z"/></svg>
          555 014 2273
        </li>
        <li class="details__item">
          <svg class="details__icon" viewBox="0 0 24 24" aria-hidden="true"><path d="M2 5h20v2l-10 6L2 7z M2 9l10 6 10-6v10H2z"/></svg>
          info@quietangle.com
        </li>
        <li class="details__item">
          <svg class="details__icon" viewBox="0 0 24 24" aria-hidden="true"><circle cx="12" cy="12" r="10"/></svg>
          www.quietangle.com
        </li>
      </ul>
    </div>
    <p class="address">418, Meridian Avenue, Brooklyn NY 11299</p>
    <div class="card__edge"></div>
  </section>

</main>
</body>
</html>
```